Catering Menu Package

I currently have a complete menu package, which we have redesigned as far as content, now I need to it put together in a catalog type format. It is essentially 10-12 pages in length, and will be sent for print production. Upon receiving a final edit
Updates

I have added an example gif to the project.

I did this free hand this basically what I am looking for. please change text and type to whatever you think would look best. This is a total rough design so, feel free to change any and everything. The text for the page is on the word documents. If you need more images let me know I am in the process of getting as many images uploaded for your use.

Project Deadline Extended
Reason: I figured we got a late jump with questions, so i am extending a few days .

Target Market(s)

The target market is business who wish to have catered luncheons, breakfasts , meetings

Industry/Entity Type

Catering

Requirements
Must have
• I have attached a copy of the text that what we want in the package, our logo, and i have also attached a catering package of another company to give you an idea what the finished product will be
Should not have
• It should not look identical to the example catering packages, these are for some inspiration we want our own design with the same type of look and feel

```html
<!DOCTYPE html>
<html lang="en">
<head>
<meta charset="utf-8">
<title>Sample Cocktail Hour and Reception Menus</title>
<link href="https://fonts.googleapis.com/css2?family=Pinyon+Script&family=Kurale&display=swap" rel="stylesheet">
<style>
  :root {
    --paper: #ebe5d9;
    --ink: #1b1714;
    --rule: #111111;
    --accent: #e8782a;
  }
  * { margin: 0; padding: 0; box-sizing: border-box; }
  html, body { width: 1200px; height: 928px; overflow: hidden; }
  body { background: var(--paper); color: var(--ink); font-family: "Kurale", Georgia, serif; }
  .menu-page { position: relative; width: 1200px; height: 928px; overflow: hidden; }
  .page-texture { position: absolute; inset: 0; background: var(--paper); }
  .page-title {
    position: absolute; top: 52px; left: 0; width: 100%;
    text-align: center; font-family: "Pinyon Script", cursive;
    font-size: 44px; font-weight: 400;
  }
  .menu-column { position: absolute; top: 136px; text-align: right; }
  .menu-column--sampler { left: 40px; width: 544px; }
  .menu-column--artisan { left: 630px; width: 536px; }
  .menu-heading {
    font-family: "Pinyon Script", cursive; font-weight: 400;
    font-size: 46px; line-height: 60px; margin-bottom: 2px;
  }
  .menu-items { list-style: none; font-size: 17.5px; line-height: 31.7px; }
  .menu-items .multi-line { line-height: 20px; padding: 6px 0 6px; }
  .column-divider {
    position: absolute; left: 610px; top: 138px; width: 3px; height: 694px;
    background: var(--rule);
  }
  .brand-mark {
    position: absolute; left: 64px; top: 700px; width: 140px;
    display: flex; flex-direction: column; align-items: center; gap: 10px;
  }
  .brand-dot { width: 60px; height: 60px; border-radius: 50%; background: var(--accent); }
  .brand-name { font-size: 17px; line-height: 21px; text-align: center; color: var(--ink); }
</style>
</head>
<body>
<main class="menu-page">
  <div class="page-texture" role="img" aria-label="Faint cream swirling floral background pattern"></div>

  <h1 class="page-title">Sample Cocktail Hour and Reception Menus</h1>

  <section class="menu-column menu-column--sampler">
    <h2 class="menu-heading">The Sampler</h2>
    <ul class="menu-items">
      <li>Assorted Miniature Sandwiches</li>
      <li>Oven Roasted Turkey, Black Forest Ham &amp; Roasted Top Round of Beef</li>
      <li>Served on Artisan rolls &amp; fresh baked baguette</li>
      <li>Served with Mayonaise, Mustard, Dijon, And Horseradish</li>
      <li>Rotisserie Roasted Chicken Drummies &amp; Wing Sections</li>
      <li>Served with sweet &amp; sour, hot sauce &amp; chipotle ranch</li>
      <li>With celery and carrot stalks</li>
      <li>Cranberry BBQ Meatballs</li>
      <li>Fresh Fruit &amp; Melon Display</li>
      <li>Vegetable Pasta Salad</li>
      <li>Maryland Crab Dip</li>
      <li>Served with Gourmet Crackers</li>
    </ul>
  </section>

  <div class="column-divider"></div>

  <section class="menu-column menu-column--artisan">
    <h2 class="menu-heading">The Artisan</h2>
    <ul class="menu-items">
      <li>An Artfully Displayed Hors’doeuvre Table including the following:</li>
      <li>Artisan Rolls and Breads</li>
      <li>Lavosh, Assorted Gourmet Crackers, and Crostinis Pita Bread</li>
      <li>Wedges and &nbsp;Baguette Loafs</li>
      <li>Fresh Grapes and Strawberries</li>
      <li>Seasonal fruit</li>
      <li>Garden Fresh Vegetables</li>
      <li>Grilled and marinated in Aged Imported Balsamic Vinegar.</li>
      <li class="multi-line">A Variety of Artesian Cheeses, including but not limited Cheddar,<br>Havarti, Goat Cheese, Gorgonzola, Smoked Gouda, Pepper-Jack, and<br>Brie accompanied with assorted dried fruit and nuts.</li>
      <li>Various Imported Olives and Pickled Vegetables</li>
      <li>Aged Salami, Italian Hams, and Pepperoni.</li>
      <li>Hummus and Olive Tapenades</li>
      <li>Infused Olive Oils</li>
    </ul>
  </section>

  <div class="brand-mark">
    <span class="brand-dot"></span>
    <span class="brand-name">Meadowbrook<br>Caterers</span>
  </div>
</main>
</body>
</html>
```